Luxury Candle Startup Needs Modern Packaging Box & Matching Label Design

We are Lumavale, a luxury candle company about to launch in Australia and we need a box packaging design that is modern, minimalist, and feminine. Our target audience are females, mostly mothers, within the age range of 25-45 who are looking for high quality, handmade luxurious products. Our company is going to have a large social media presence with new mothers as we are going to show our journey with starting a business whilst on maternity leave. We would like the arch shape incorporated into the box packaging as it is beautiful and symbolises moving into a new phase in life which really represents the brand. We would like for the packaging box to be a simple white box with a sleeve insert over the box with the design to make printing easier. Our colour inspiration are very earthy colours and would like the sleeve colour to be easily changed according to the scent. For example dusky rose coloured sleeve for rose patchouli and amber scent, light coffee coloured sleeve for coffee bean cacao scent etc. Please see uploaded files for inspiration, our logo, and the type of candle jars used.
The box dimensions are:
External Dimension: 95mmW x 95mmL x 116mmH
We look forward to seeing your amazing designs!

```html
<!DOCTYPE html>
<html lang="en">
<head>
<meta charset="UTF-8">
<title>Lumavale – Rose Patchouli Sleeve</title>
<link rel="stylesheet" href="https://fonts.googleapis.com/css2?family=Cormorant+Garamond:wght@500&family=Montserrat:wght@600&family=Lato:wght@300&display=swap">
<style>
  :root {
    --canvas-bg: #f2f2f2;
    --sleeve-rose: #f9cdcf;
    --ink-plum: #6e4149;
    --illustration-tone: #f2b9bd;
    --illustration-soft: #f6c4c7;
  }
  * { margin: 0; padding: 0; box-sizing: border-box; }
  html, body {
    width: 1200px;
    height: 1200px;
    overflow: hidden;
    background: var(--canvas-bg);
  }
  .canvas {
    position: relative;
    width: 1200px;
    height: 1200px;
    display: flex;
    align-items: center;
  }
  .sleeve {
    position: relative;
    width: 1200px;
    height: 330px;
    background: var(--sleeve-rose);
  }
  .sleeve__illustration {
    position: absolute;
    left: 300px;
    top: 12px;
    width: 235px;
    height: 310px;
    border-radius: 48% 52% 30% 40% / 40% 40% 30% 30%;
    background: radial-gradient(ellipse at 40% 30%, var(--illustration-tone) 0%, var(--illustration-soft) 45%, var(--sleeve-rose) 75%);
    opacity: 0.7;
  }
  .sleeve__brand {
    position: absolute;
    left: 496px;
    top: 66px;
    width: 334px;
    text-align: center;
    color: var(--ink-plum);
  }
  .brand-name {
    font-family: "Cormorant Garamond", serif;
    font-weight: 500;
    font-size: 58px;
    line-height: 1;
    letter-spacing: 2px;
    text-transform: uppercase;
  }
  .brand-tagline {
    margin-top: 18px;
    font-family: "Montserrat", sans-serif;
    font-weight: 600;
    font-size: 10.5px;
    letter-spacing: 1.8px;
    text-transform: uppercase;
  }
  .brand-origin {
    margin-top: 5px;
    font-family: "Montserrat", sans-serif;
    font-weight: 600;
    font-size: 7.5px;
    letter-spacing: 1.6px;
    text-transform: uppercase;
  }
  .scent-name {
    margin-top: 15px;
    font-family: "Lato", sans-serif;
    font-weight: 300;
    font-size: 21px;
    letter-spacing: 0.5px;
    text-transform: uppercase;
  }
</style>
</head>
<body>
  <main class="canvas">
    <section class="sleeve">
      <div class="sleeve__illustration" role="img" aria-label="Fine line drawing of a rose bloom with stem and leaf in soft pink"></div>
      <div class="sleeve__brand">
        <h1 class="brand-name">Lumavale</h1>
        <p class="brand-tagline">Luxury Fragrance</p>
        <p class="brand-origin">Australia</p>
        <p class="scent-name">Rose Patchouli</p>
      </div>
    </section>
  </main>
</body>
</html>
```